Velvet Riot Rising Line of Sparkling Wine & Spirits

Back info: Nora Beth Quill Owner 555-318-4402 1480 E. Harlow Ave, Bldg. 2, & 3, Lodi Ca. 95871
Sparkling Wines & Memorabilia www.velvetriotrising.com
Ok I have uploaded the winning design. The color that I am after is the Fushia, Raspberry, Red, Matte Satin Matalic Finish. With a 24 Karet Gold color Foil. The Bottle is on the top row and it's the 2nd Bottle in. That is the Color that I want. This is the style of font. Make sure that you put what we're advertising. Good Luck to you all. Warmest regards, Nora
21 & up UniSex
Sparkling Wine and Memorabilia
there listed up above.....

```html
<!DOCTYPE html>
<html lang="en">
<head>
<meta charset="utf-8">
<title>Velvet Riot Rising – Business Cards</title>
<link rel="stylesheet" href="https://fonts.googleapis.com/css2?family=Poppins:wght@400;600&family=Pirata+One&display=swap">
<style>
  :root {
    --bg: #2a2a2b;
    --fuchsia-deep: #9c0f57;
    --fuchsia-mid: #c3137a;
    --fuchsia-bright: #e2198f;
    --gold: #e0b12a;
    --gold-edge: #d6a516;
    --ink: #111014;
  }
  * { margin: 0; padding: 0; box-sizing: border-box; }
  html, body { width: 1200px; height: 689px; overflow: hidden; background: var(--bg); }
  .canvas {
    position: relative; width: 1200px; height: 689px;
    display: flex; align-items: center; justify-content: center; gap: 48px;
    font-family: "Poppins", sans-serif;
  }
  .card {
    position: relative; width: 528px; height: 302px; border-radius: 22px;
    border: 2px solid var(--gold-edge);
    background: linear-gradient(160deg, var(--fuchsia-deep) 0%, var(--fuchsia-bright) 48%, var(--fuchsia-mid) 72%, var(--fuchsia-deep) 100%);
    color: var(--gold);
  }
  .card--front { display: flex; flex-direction: column; align-items: center; justify-content: center; }
  .brand-name { font-family: "Poppins", sans-serif; font-weight: 600; letter-spacing: 0.5px; }
  .card--front .brand-name { color: var(--ink); font-size: 40px; line-height: 1.1; }
  .tagline { margin-top: 34px; font-size: 13px; letter-spacing: 1.6px; text-transform: uppercase; }
  .card--back .brand-name {
    position: absolute; top: 38px; right: 34px; font-size: 24px; color: var(--gold);
  }
  .owner { position: absolute; left: 40px; top: 96px; }
  .owner__name { font-family: "Pirata One", serif; font-size: 34px; line-height: 1; }
  .owner__role { font-size: 14px; margin-top: 4px; }
  .address { position: absolute; left: 40px; top: 172px; font-size: 13px; line-height: 1.35; }
  .contacts { position: absolute; left: 40px; bottom: 26px; list-style: none; font-size: 13px; line-height: 1.45; }
  .contacts li { display: flex; align-items: center; gap: 8px; }
  .contacts svg { width: 13px; height: 13px; flex: none; }
</style>
</head>
<body>
<main class="canvas">
  <section class="card card--front">
    <h1 class="brand-name">Velvet Riot Rising</h1>
    <p class="tagline">Sparkling Wines &amp; Memorabilia</p>
  </section>

  <section class="card card--back">
    <p class="brand-name">Velvet Riot Rising</p>
    <div class="owner">
      <p class="owner__name">Nora Beth Quill</p>
      <p class="owner__role">Owner</p>
    </div>
    <address class="address">
      1480 E. Harlow Ave, Bldg. 2, &amp; 3,<br>
      Lodi Ca. 95871
    </address>
    <ul class="contacts">
      <li>
        <svg viewBox="0 0 16 16" aria-hidden="true"><path fill="currentColor" d="M3.6 1.2l2.2 2.6-1.3 1.8c.9 2 2.6 3.7 4.6 4.6l1.8-1.3 2.6 2.2-1.4 2.6C6.7 13.5 2.5 9.3 1 3l2.6-1.8z"/></svg>
        555-318-4402
      </li>
      <li>
        <svg viewBox="0 0 16 16" aria-hidden="true"><rect x="1" y="3" width="14" height="10" rx="1" fill="currentColor"/><path d="M1.5 3.8L8 9l6.5-5.2" fill="none" stroke="#b0126a" stroke-width="1.3"/></svg>
        thequeen@velvetriotrising.com
      </li>
      <li>
        <svg viewBox="0 0 16 16" aria-hidden="true"><g fill="none" stroke="currentColor" stroke-width="1.3"><circle cx="8" cy="8" r="6.5"/><ellipse cx="8" cy="8" rx="2.8" ry="6.5"/><path d="M1.5 8h13M2.5 4.8h11M2.5 11.2h11"/></g></svg>
        www.velvetriotrising.com
      </li>
    </ul>
  </section>
</main>
</body>
</html>
```